New Business Card Design for Manufacturing

We are an engineering/manufacturing company that offers Advanced machining/assembly/engineering services, as well as innovative products for the heavy duty engine cooling markets.

We are looking to get a new business card designed that is clean and modern looking, but still fits the wide range of technical/skilled work we do.

- We hope to use this design as the base for other design work in new Presentations, web, and print work.

Industry/Entity Type

Engineering

Contact Information for Business Card

Our preferred color of blue is (RGB) 22/71/159 but can vary slightly from that color. Our content will be our Logo and full company name (Vantrell Forge Works, Inc.), company address, name, job title, phone number with extension, cell number, fax number, website, and email address on the cards.
We'd like the full company name next to the logo, but we are open to other interpretations of that layout.
Preferably, we would like the back side to be clean with just our logo, and the front to contain all of the contact information.

Colors
2f74b4
0355a3
85abd2

Requirements
Must have
• - Logo, company name, needed content - We are open to interpretation beyond that.
• - Standard size business card.
• - Horizontal orientation.
• - Enough space for lengthy names / job titles (for example, a job title could read "Directory of Human Resources" or "V.P. of Governmental Affairs"). We need this to look clean, whether the title be short (CEO) or long (as described above).

```html
<!DOCTYPE html>
<html lang="en">
<head>
<meta charset="utf-8">
<title>Vantrell Forge Works – Business Card</title>
<link rel="stylesheet" href="https://fonts.googleapis.com/css2?family=Roboto:wght@400;700;900&family=Roboto+Condensed:wght@700&display=swap">
<style>
  :root {
    --brand-blue: #0f52a1;
    --paper: #f2f2f2;
    --stage: #2a2a2a;
    --ink: #111111;
    --ink-soft: #4a4a4a;
    --tagline-grey: #8a8a8a;
    --white: #ffffff;
  }
  * { margin: 0; padding: 0; box-sizing: border-box; }
  html, body { width: 1200px; height: 960px; overflow: hidden; }
  body {
    background: var(--stage);
    font-family: "Roboto", Arial, sans-serif;
    position: relative;
  }
  .card {
    position: absolute;
    width: 600px;
    height: 343px;
  }
  .card--front { left: 314px; top: 113px; background: var(--paper); }
  .card--back  { left: 311px; top: 472px; background: var(--brand-blue); }

  .brand { position: absolute; left: 51px; top: 58px; }
  .brand__name {
    font-family: "Roboto", Arial, sans-serif;
    font-weight: 900;
    font-size: 50px;
    line-height: 1;
    letter-spacing: 0.5px;
    color: var(--brand-blue);
    text-transform: uppercase;
  }
  .brand__tagline {
    margin-top: 8px;
    font-weight: 700;
    font-size: 14px;
    letter-spacing: 0.3px;
    color: var(--tagline-grey);
    text-transform: uppercase;
  }

  .person { position: absolute; left: 51px; top: 216px; }
  .person__name {
    font-family: "Roboto Condensed", "Arial Narrow", sans-serif;
    font-weight: 700;
    font-size: 24px;
    line-height: 1;
    color: var(--brand-blue);
    text-transform: uppercase;
  }
  .person__title {
    margin-top: 5px;
    font-size: 14px;
    color: var(--ink);
  }

  .contact {
    position: absolute;
    left: 378px;
    top: 175px;
    font-size: 14px;
    color: var(--ink-soft);
    line-height: 19px;
  }
  .contact__address { margin-bottom: 7px; }
  .contact__list { list-style: none; }
  .contact__item { display: flex; align-items: center; gap: 9px; }
  .contact__icon { width: 13px; height: 13px; flex: none; fill: var(--brand-blue); }

  .back-lockup {
    position: absolute;
    left: 0; right: 0; top: 132px;
    display: flex;
    align-items: center;
    justify-content: center;
    gap: 14px;
  }
  .back-lockup__mark { width: 22px; height: 22px; background: var(--white); }
  .back-lockup__name {
    font-weight: 900;
    font-size: 26px;
    line-height: 1.05;
    color: var(--white);
    text-transform: uppercase;
  }
  .back-lockup__tagline {
    margin-top: 6px;
    font-weight: 700;
    font-size: 13px;
    color: var(--white);
    text-transform: uppercase;
  }
</style>
</head>
<body>

<section class="card card--front">
  <div class="brand">
    <div class="brand__name">Vantrell</div>
    <div class="brand__tagline">Built to Endure</div>
  </div>

  <div class="person">
    <div class="person__name">Daniel Harrow</div>
    <div class="person__title">V.P. of Governmental Affairs</div>
  </div>

  <div class="contact">
    <div class="contact__address">4120 Linden Court<br>Anchorage, Alaska 34512</div>
    <ul class="contact__list">
      <li class="contact__item">
        <svg class="contact__icon" viewBox="0 0 24 24"><path d="M6.6 10.8a15.1 15.1 0 0 0 6.6 6.6l2.2-2.2a1 1 0 0 1 1-.25 11.4 11.4 0 0 0 3.6.6 1 1 0 0 1 1 1V20a1 1 0 0 1-1 1A17 17 0 0 1 3 4a1 1 0 0 1 1-1h3.5a1 1 0 0 1 1 1c0 1.25.2 2.45.6 3.6a1 1 0 0 1-.25 1z"/></svg>
        <span>555 210 4471</span>
      </li>
      <li class="contact__item">
        <svg class="contact__icon" viewBox="0 0 24 24"><path d="M7 1h10a2 2 0 0 1 2 2v18a2 2 0 0 1-2 2H7a2 2 0 0 1-2-2V3a2 2 0 0 1 2-2zm0 3v14h10V4zm5 15.5a1.2 1.2 0 1 0 0 2.4 1.2 1.2 0 0 0 0-2.4z"/></svg>
        <span>555 318 6620</span>
      </li>
      <li class="contact__item">
        <svg class="contact__icon" viewBox="0 0 24 24"><path d="M2 5h20v14H2zm2 2v.5l8 5 8-5V7zm0 3v7h16v-7l-8 5z"/></svg>
        <span>daniel@vantrellforge.com</span>
      </li>
      <li class="contact__item">
        <svg class="contact__icon" viewBox="0 0 24 24"><circle cx="12" cy="12" r="10"/></svg>
        <span>www.vantrellforge.com</span>
      </li>
    </ul>
  </div>
</section>

<section class="card card--back">
  <div class="back-lockup">
    <div class="back-lockup__mark"></div>
    <div>
      <div class="back-lockup__name">Vantrell<br>Forge Works, Inc.</div>
      <div class="back-lockup__tagline">Built to Endure</div>
    </div>
  </div>
</section>

</body>
</html>
```